Provide bookkeeping and accounting services to small and growing businesses

We need website and logo design using the name Dornaby as the logo.
The target audience are small companies and startups who need:
1) Simple bookkeeping services
2) Accounting advice that only someone with many years of senior financial experience as a CPA can provide.

The services are provided by two individuals. each of whom specialize in one of the areas.

We want the website to be clean without a lot of visual distraction but don't know how to make a boring subject interesting. We believe our potential clients, small business owners, need to find what they want quickly and easily without a lot of verbiage or distractions.

We've attached a draft of the homepage and have completed the text on most of the other pages.

Target Market(s)

small and early stage growth companies in San Diego North County

Industry/Entity Type

Accounting

Number of Pages Required

1 page

Font styles to use
Sans Serif

Colors
86cfc6
33b8a4
85cae6

Requirements
Must have
• We need a design for the website homepage that includes the name Dornaby as the logo. Must include a design for the name.
• Must have color in teal or greenish blue.
Nice to have
• White background, clean, clear, uncluttered.
• We would like to use the design in a Theme on a WordPress website. Themes Paper Lantern and Quiet Harbour are appealing to us.
Should not have
• Moving pictures

```html
<!DOCTYPE html>
<html lang="en">
<head>
<meta charset="utf-8">
<title>Dornaby Accounting &amp; Bookkeeping</title>
<link rel="stylesheet" href="https://fonts.googleapis.com/css2?family=Raleway:wght@500;600;700&family=Open+Sans:ital,wght@0,400;0,600;0,700;1,400&display=swap">
<style>
:root{
  --teal:#33b8a4;
  --teal-soft:#86cfc6;
  --sky:#85cae6;
  --ink:#1f2328;
  --text:#555b60;
  --muted:#8a8f94;
  --dark:#262b33;
  --line:#e3e5e7;
  --white:#ffffff;
}
*{box-sizing:border-box;margin:0;padding:0}
html,body{width:1200px;height:2344px;overflow:hidden;background:var(--white)}
body{position:relative;font-family:"Open Sans",Arial,sans-serif;color:var(--text)}
.abs{position:absolute}
.heading{font-family:"Raleway",Arial,sans-serif;font-weight:700;color:var(--ink)}

/* header */
.top-rule{left:0;top:0;width:1200px;height:5px;background:var(--sky)}
.site-header{left:0;top:5px;width:1200px;height:73px;background:var(--white)}
.brand{left:98px;top:10px;display:flex;align-items:center;gap:14px}
.brand-mark{width:58px;height:58px;border-radius:50%;background:var(--teal)}
.brand-name{font-family:"Raleway",Arial,sans-serif;font-weight:700;font-size:30px;color:var(--ink);letter-spacing:.3px}
.contact-strip{right:98px;top:15px;display:flex;gap:26px;font-size:14px;color:var(--ink)}
.contact-strip span{display:flex;align-items:center;gap:10px}
.main-nav{right:98px;top:52px;display:flex;gap:29px;font-family:"Raleway",Arial,sans-serif;font-weight:700;font-size:13px;color:var(--ink);align-items:center}
.main-nav .current{color:var(--teal)}

/* hero */
.hero{left:0;top:78px;width:1200px;height:438px;background:linear-gradient(180deg,#9cb8cf 0%,#b8cadb 40%,#7f8f9c 62%,#5c7080 78%,#8aa0b0 100%)}
.hero-title{left:0;top:196px;width:1200px;text-align:center;font-family:"Raleway",Arial,sans-serif;font-weight:700;font-size:44px;color:var(--white);text-shadow:0 2px 4px rgba(0,0,0,.35)}
.hero-sub{left:0;top:256px;width:1200px;text-align:center;font-size:23px;line-height:32px;color:var(--white);text-shadow:0 1px 3px rgba(0,0,0,.4)}
.btn{display:flex;align-items:center;justify-content:center;background:var(--teal);border:2px solid var(--white);color:var(--white);font-weight:700;font-size:16px;letter-spacing:.3px}
.hero .btn,.hero-btn{left:450px;top:339px;width:302px;height:47px}
.slider-dots{left:548px;top:470px;display:flex;gap:6px}
.slider-dots i{display:block;width:24px;height:5px;border-radius:3px;background:var(--white)}
.slider-dots i.on{background:var(--teal)}

/* welcome */
.welcome-title{left:0;top:548px;width:1200px;text-align:center;font-size:27px}
.welcome-text{left:114px;top:596px;width:972px;text-align:center;font-size:12.5px;line-height:24px}
.service{top:672px;width:240px;text-align:center}
.service svg{display:block;margin:0 auto}
.service h3{font-family:"Raleway",Arial,sans-serif;font-weight:700;font-size:19px;color:var(--ink);margin-top:20px}
.service p{font-size:12.5px;line-height:23px;margin-top:9px}
.read-more{font-weight:700;font-size:13px;color:var(--teal);letter-spacing:.3px}
.service .read-more{display:block;margin-top:12px}

/* banner */
.banner{left:0;top:939px;width:1200px;height:230px;background:linear-gradient(100deg,#6f757c 0%,#a9adb1 45%,#c9ccce 70%,#9aa0a5 100%)}
.banner-text{left:0;top:978px;width:1200px;text-align:center;font-family:"Raleway",Arial,sans-serif;font-weight:700;font-size:25px;line-height:37px;color:var(--white);text-shadow:0 1px 3px rgba(0,0,0,.35)}
.banner-btn{left:450px;top:1072px;width:302px;height:47px}

/* different + news */
.section-title{font-size:27px}
.diff-title{left:98px;top:1208px}
.diff-photo{left:98px;top:1269px;width:375px;height:211px;border:4px solid #fff;box-shadow:0 0 0 1px var(--line);background:linear-gradient(135deg,#c8dbe9 0%,#eef3f7 50%,#b9cddd 100%)}
.diff-text{left:98px;top:1492px;width:380px;font-size:12.5px;line-height:22px}
.checklist{left:98px;top:1552px;list-style:none;font-size:12.5px}
.checklist li{display:flex;align-items:center;gap:12px;height:31px}
.diff-more{left:98px;top:1688px}
.news-title{left:522px;top:1208px}
.news-item{left:522px;width:580px;height:137px;border-bottom:2px solid var(--line)}
.news-thumb{position:absolute;left:3px;top:0;width:109px;height:100px;border:3px solid #fff;box-shadow:0 0 0 1px var(--line)}
.news-body{position:absolute;left:140px;top:0;width:440px}
.news-body h4{font-family:Arial,Helvetica,sans-serif;font-weight:700;font-size:14px;color:var(--ink);letter-spacing:.2px}
.news-date{display:flex;align-items:center;gap:8px;font-size:12px;color:var(--sky);margin-top:8px}
.news-body p{font-size:12.5px;line-height:22px;margin-top:8px}
.news-more{left:528px;top:1684px}

/* testimonial */
.testimonial{left:0;top:1747px;width:1200px;height:159px;background:var(--teal)}
.quote-disc{left:150px;top:1770px;width:110px;height:110px;border-radius:50%;background:#e4e4e4}
.quote-mark{left:172px;top:1790px;font-family:Georgia,serif;font-size:90px;line-height:90px;color:#c9c9c9}
.portrait{left:220px;top:1770px;width:110px;height:110px;border-radius:50%;border:3px solid #e4e4e4;background:linear-gradient(180deg,#d8dadb 0%,#b8bcc0 100%)}
.quote-text{left:364px;top:1772px;width:690px;font-style:italic;font-size:13px;line-height:23px;color:var(--white)}
.quote-name{left:364px;top:1866px;font-family:"Raleway",Arial,sans-serif;font-weight:700;font-size:15px;color:var(--white)}
.arrow{top:1813px}

/* contact */
.contact{left:0;top:1906px;width:1200px;height:367px;background:var(--dark)}
.contact-title{left:0;top:1940px;width:1200px;text-align:center;font-family:"Raleway",Arial,sans-serif;font-weight:600;font-size:25px;color:var(--white)}
.col-label{font-family:"Raleway",Arial,sans-serif;font-weight:700;font-size:15px;color:var(--white);text-transform:uppercase}
.field{background:var(--white);font-size:11px;color:#777;padding:9px 12px;letter-spacing:.3px}
.submit{left:625px;top:2202px;width:103px;height:40px;border:2px solid var(--white);color:var(--white);font-weight:700;font-size:12px;display:flex;align-items:center;justify-content:center}
.info-row{left:786px;display:flex;align-items:center;gap:30px;font-size:14px;line-height:23px;color:var(--white)}
.info-icon{width:36px;height:36px;border-radius:50%;border:2px solid var(--white);display:flex;align-items:center;justify-content:center;flex:none}

/* footer */
.copyright{left:98px;top:2301px;font-size:11.5px;color:#666}
.social{left:998px;top:2293px;display:flex;gap:14px}
.social i{display:block;width:24px;height:24px;border-radius:3px;background:#8d9196}
</style>
</head>
<body>

<div class="abs top-rule"></div>
<header class="abs site-header">
  <div class="abs brand" style="left:98px;top:5px">
    <div class="brand-mark"></div>
    <div class="brand-name">Dornaby</div>
  </div>
  <div class="abs contact-strip" style="top:10px">
    <span>
      <svg width="22" height="22" viewBox="0 0 22 22"><circle cx="11" cy="11" r="10" fill="none" stroke="#33b8a4" stroke-width="2"/><path d="M7.5 6.5l2 0 1 2.5-1.3 1c.6 1.3 1.5 2.2 2.8 2.8l1-1.3 2.5 1v2c-4.5.3-8.3-3.5-8-8z" fill="#33b8a4"/></svg>
      1 760 555 0142
    </span>
    <span>
      <svg width="22" height="22" viewBox="0 0 22 22"><circle cx="11" cy="11" r="11" fill="#33b8a4"/><rect x="5.5" y="7" width="11" height="8" rx="1" fill="#fff"/><path d="M5.5 7.5l5.5 4 5.5-4" fill="none" stroke="#33b8a4" stroke-width="1.2"/></svg>
      info@dornaby.com
    </span>
  </div>
  <nav class="abs main-nav" style="top:47px">
    <span class="current">HOME</span>
    <span>ABOUT US</span>
    <span>SERVICES</span>
    <span>EXPERIENCE</span>
    <span>RESOURCES</span>
    <span>CONTACT US</span>
    <svg width="13" height="13" viewBox="0 0 13 13"><circle cx="5.3" cy="5.3" r="4" fill="none" stroke="#1f2328" stroke-width="2"/><path d="M8.3 8.3l3.7 3.7" stroke="#1f2328" stroke-width="2.2"/></svg>
  </nav>
</header>

<section class="abs hero" role="img" aria-label="Waterfront city skyline with high-rise towers reflected in the bay"></section>
<h1 class="abs hero-title">Dornaby Accounting &amp; Bookkeeping</h1>
<p class="abs hero-sub">We simple book keeping services, financial and accounting<br>advice for small start up companies</p>
<div class="abs btn hero-btn">REQUEST A FREE CONSULTATION</div>
<div class="abs slider-dots"><i class="on"></i><i></i><i></i><i></i></div>

<h2 class="abs heading welcome-title">Welcome to Dornaby Accounting &amp; Bookkeeping</h2>
<p class="abs welcome-text">Dornaby offers a flexible range of accounting and bookkeeping services and support for small and growing organizations in San Diego North County. We provide bookkeeping services specializing in Tallybook® at your offices or remotely from ours. We also &nbsp;provide a broad range of accounting services or financial advice.</p>

<div class="abs service" style="left:78px">
  <svg width="80" height="86" viewBox="0 0 80 86"><rect x="24" y="22" width="46" height="52" rx="3" fill="none" stroke="#85cae6" stroke-width="3"/><path d="M24 30h20l4-8h22" fill="none" stroke="#85cae6" stroke-width="3"/><circle cx="28" cy="30" r="18" fill="#fff" stroke="#33b8a4" stroke-width="3"/><rect x="18" y="22" width="20" height="16" rx="2" fill="none" stroke="#33b8a4" stroke-width="2.5"/><path d="M22 27h12M22 31h12M22 35h8" stroke="#33b8a4" stroke-width="2"/></svg>
  <h3>Book Keeping</h3>
  <p>We provide bookkeeping services<br>specializing in Tallybook® at your<br>offices or remotely from ours.</p>
  <span class="read-more">READ MORE &gt;&gt;</span>
</div>
<div class="abs service" style="left:344px">
  <svg width="80" height="86" viewBox="0 0 80 86"><text x="48" y="42" text-anchor="middle" font-family="Raleway,Arial,sans-serif" font-weight="700" font-size="44" fill="#33b8a4">$</text><path d="M4 58h16c6 0 10 4 18 4h14c3 0 3 5 0 5H36l26-2 12-8c3-2 6 1 4 4L62 74H4z" fill="#85cae6"/></svg>
  <h3>Financial</h3>
  <p>We provide bookkeeping services<br>specializing in Tallybook® at your<br>offices or remotely from ours.</p>
  <span class="read-more">READ MORE &gt;&gt;</span>
</div>
<div class="abs service" style="left:613px">
  <svg width="80" height="86" viewBox="0 0 80 86"><text x="16" y="36" text-anchor="middle" font-family="Raleway,Arial,sans-serif" font-weight="700" font-size="36" fill="#33b8a4">$</text><rect x="26" y="18" width="40" height="60" rx="3" fill="none" stroke="#85cae6" stroke-width="3"/><rect x="32" y="25" width="28" height="11" fill="#85cae6"/><g fill="#85cae6"><rect x="32" y="42" width="7" height="6"/><rect x="42.5" y="42" width="7" height="6"/><rect x="53" y="42" width="7" height="6"/><rect x="32" y="53" width="7" height="6"/><rect x="42.5" y="53" width="7" height="6"/><rect x="53" y="53" width="7" height="6"/><rect x="32" y="64" width="7" height="6"/><rect x="42.5" y="64" width="7" height="6"/><rect x="53" y="64" width="7" height="6"/></g></svg>
  <h3>Accounting</h3>
  <p>We provide bookkeeping services<br>specializing in Tallybook® at your<br>offices or remotely from ours.</p>
  <span class="read-more">READ MORE &gt;&gt;</span>
</div>
<div class="abs service" style="left:880px">
  <svg width="80" height="86" viewBox="0 0 80 86"><circle cx="40" cy="34" r="16" fill="#85cae6"/><path d="M18 78c0-14 10-22 22-22s22 8 22 22z" fill="#85cae6"/><path d="M20 36c0-14 9-22 20-22s20 8 20 22" fill="none" stroke="#33b8a4" stroke-width="4"/><rect x="15" y="32" width="8" height="13" rx="3" fill="#33b8a4"/><rect x="57" y="32" width="8" height="13" rx="3" fill="#33b8a4"/><path d="M61 45c0 6-6 9-13 9" fill="none" stroke="#33b8a4" stroke-width="3"/></svg>
  <h3>Support</h3>
  <p>We provide bookkeeping services<br>specializing in Tallybook® at your<br>offices or remotely from ours.</p>
  <span class="read-more">READ MORE &gt;&gt;</span>
</div>

<section class="abs banner" role="img" aria-label="Hand holding a pen over printed financial charts and reports"></section>
<p class="abs banner-text">We provide bookkeeping services specializing<br>in Tallybook® at your offices or remotely from ours.</p>
<div class="abs btn banner-btn">REQUEST A FREE CONSULTATION</div>

<h2 class="abs heading section-title diff-title">What Makes Us Different</h2>
<div class="abs diff-photo" role="img" aria-label="Hand with a pencil checking figures on a spreadsheet"></div>
<p class="abs diff-text">We also provide a broad range of accounting services or financial advice &amp; provide bookkeeping services specializing in Tallybook®</p>
<ul class="abs checklist">
  <li><svg width="14" height="14" viewBox="0 0 14 14"><circle cx="7" cy="7" r="7" fill="#85cae6"/><path d="M3.8 7.2l2.2 2.2 4.2-4.4" fill="none" stroke="#fff" stroke-width="1.8"/></svg>22% higher profitability</li>
  <li><svg width="14" height="14" viewBox="0 0 14 14"><circle cx="7" cy="7" r="7" fill="#85cae6"/><path d="M3.8 7.2l2.2 2.2 4.2-4.4" fill="none" stroke="#fff" stroke-width="1.8"/></svg>21% higher productivity</li>
  <li><svg width="14" height="14" viewBox="0 0 14 14"><circle cx="7" cy="7" r="7" fill="#85cae6"/><path d="M3.8 7.2l2.2 2.2 4.2-4.4" fill="none" stroke="#fff" stroke-width="1.8"/></svg>37% lower absenteeism</li>
  <li><svg width="14" height="14" viewBox="0 0 14 14"><circle cx="7" cy="7" r="7" fill="#85cae6"/><path d="M3.8 7.2l2.2 2.2 4.2-4.4" fill="none" stroke="#fff" stroke-width="1.8"/></svg>Up to 65% less turnover of staff.</li>
</ul>
<span class="abs read-more diff-more">READ MORE &gt;&gt;</span>

<h2 class="abs heading section-title news-title">Our News</h2>
<article class="abs news-item" style="top:1269px">
  <div class="news-thumb" role="img" aria-label="Business people talking by an office window" style="background:linear-gradient(180deg,#d9dde0,#6c6f72)"></div>
  <div class="news-body">
    <h4>AT VERO EOS ET ACCUSAMUS ET IUSTO ODIO DIG</h4>
    <div class="news-date"><svg width="12" height="12" viewBox="0 0 12 12"><rect x="1" y="2" width="10" height="9" fill="none" stroke="#85cae6" stroke-width="1.5"/><path d="M1 5h10M4 0v3M8 0v3" stroke="#85cae6" stroke-width="1.5"/></svg>05/03/2016</div>
    <p>Nemo enim ipsam voluptatem quia voluptas sit aspernatur aut odit aut fugit, sed quia consequuntur..</p>
  </div>
</article>
<article class="abs news-item" style="top:1406px">
  <div class="news-thumb" role="img" aria-label="Printed financial charts and tables" style="background:linear-gradient(135deg,#a8c8e8,#e6eef6)"></div>
  <div class="news-body">
    <h4>AT VERO EOS ET ACCUSAMUS ET IUSTO ODIO DIG</h4>
    <div class="news-date"><svg width="12" height="12" viewBox="0 0 12 12"><rect x="1" y="2" width="10" height="9" fill="none" stroke="#85cae6" stroke-width="1.5"/><path d="M1 5h10M4 0v3M8 0v3" stroke="#85cae6" stroke-width="1.5"/></svg>05/03/2016</div>
    <p>Nemo enim ipsam voluptatem quia voluptas sit aspernatur aut odit aut fugit, sed quia consequuntur..</p>
  </div>
</article>
<article class="abs news-item" style="top:1543px">
  <div class="news-thumb" role="img" aria-label="Hands using a calculator over paperwork" style="background:linear-gradient(135deg,#6d9fc9,#d7e3ec)"></div>
  <div class="news-body">
    <h4>AT VERO EOS ET ACCUSAMUS ET IUSTO ODIO DIG</h4>
    <div class="news-date"><svg width="12" height="12" viewBox="0 0 12 12"><rect x="1" y="2" width="10" height="9" fill="none" stroke="#85cae6" stroke-width="1.5"/><path d="M1 5h10M4 0v3M8 0v3" stroke="#85cae6" stroke-width="1.5"/></svg>05/03/2016</div>
    <p>Nemo enim ipsam voluptatem quia voluptas sit aspernatur aut odit aut fugit, sed quia consequuntur..</p>
  </div>
</article>
<span class="abs read-more news-more">VIEW MORE &gt;&gt;</span>

<section class="abs testimonial"></section>
<svg class="abs arrow" style="left:98px" width="16" height="24" viewBox="0 0 16 24"><path d="M13 2L3 12l10 10" fill="none" stroke="#fff" stroke-width="3"/></svg>
<svg class="abs arrow" style="left:1086px" width="16" height="24" viewBox="0 0 16 24"><path d="M3 2l10 10L3 22" fill="none" stroke="#fff" stroke-width="3"/></svg>
<div class="abs quote-disc"></div>
<div class="abs quote-mark">&ldquo;</div>
<div class="abs portrait" role="img" aria-label="Portrait photo of the client giving the testimonial"></div>
<p class="abs quote-text">It is a long established fact that a reader will be distracted by the readable content of a page when looking at its layout. The point of using Lorem Ipsum is that it has a more-or-less normal distribution of letters, as opposed to using 'Content here, content here', making it look like readable English.</p>
<div class="abs quote-name">- Evan Marlow</div>

<section class="abs contact"></section>
<h2 class="abs contact-title">Contact Us</h2>
<div class="abs col-label" style="left:98px;top:1994px">Enquiry Form</div>
<div class="abs field" style="left:100px;top:2034px;width:308px;height:35px">NAME :</div>
<div class="abs field" style="left:420px;top:2034px;width:308px;height:35px">PHONE :</div>
<div class="abs field" style="left:100px;top:2080px;width:628px;height:33px">EMAIL :</div>
<div class="abs field" style="left:100px;top:2123px;width:628px;height:66px">MESSAGE :</div>
<div class="abs submit">SUBMIT</div>

<div class="abs col-label" style="left:786px;top:1994px">Contact Information</div>
<div class="abs info-row" style="top:2036px">
  <div class="info-icon"><svg width="14" height="18" viewBox="0 0 14 18"><path d="M7 1a6 6 0 0 0-6 6c0 4.5 6 10 6 10s6-5.5 6-10a6 6 0 0 0-6-6z" fill="none" stroke="#fff" stroke-width="2"/><circle cx="7" cy="7" r="2" fill="#fff"/></svg></div>
  <span>42 Palomar Crest suite 210<br>Carlsbad, CA 92008</span>
</div>
<div class="abs info-row" style="top:2098px">
  <div class="info-icon"><svg width="16" height="16" viewBox="0 0 16 16"><path d="M3 1.5h3l1.3 3.3-1.8 1.3c.8 1.8 2.1 3.1 3.9 3.9l1.3-1.8 3.3 1.3v3C8 13 3 8 3 1.5z" fill="#fff"/></svg></div>
  <span>+1 760 555 0142</span>
</div>
<div class="abs info-row" style="top:2156px">
  <div class="info-icon"><svg width="16" height="12" viewBox="0 0 16 12"><rect width="16" height="12" rx="1.5" fill="#fff"/><path d="M1 1.5l7 5 7-5" fill="none" stroke="#262b33" stroke-width="1.5"/></svg></div>
  <span>info@dornaby.com</span>
</div>

<footer>
  <p class="abs copyright">© 2016, Dornaby Accounting &amp; Bookkeeping. All Rights Reserved.</p>
  <div class="abs social"><i></i><i></i><i></i></div>
</footer>

</body>
</html>
```